KRT Flyer to attract applicants 11x17

Lantern Stagehand Collective provides crew for local concerts, filming, theater, and corporate events.
The flyer will be posted on bulletin boards at colleges with theater programs.
Our primary venues are historic theaters in downtown LA
Need a 11x17 poster to attract potential applicants/crew
I have attached a poster that one of our staff made that has all if the relevant info - but i know the poster can look much better than that. I have also attached many images and our logo. It is not necessary to use all of the images, or any of them. The two images of the theater interiors are the venues we operate so they would be the first to include. I can send additional info or images upon request. Thank you

Industry/Entity Type

Entertainment

Requirements
Must have
• APPLY@KRTCREW.EXAMPLE

```html
<!DOCTYPE html>
<html lang="en">
<head>
<meta charset="UTF-8">
<title>Lantern Stagehand Collective – Open Position</title>
<link href="https://fonts.googleapis.com/css2?family=Bebas+Neue&family=Great+Vibes&family=Poppins:wght@300;400;600;700&display=swap" rel="stylesheet">
<style>
  :root {
    --page-bg: #d9eefa;
    --paper: #fafcfe;
    --ink-light: #ffffff;
    --brand-blue: #2d57a8;
    --venue-deep: #2a1330;
    --venue-red: #6e2a26;
    --venue-violet: #4a2a5e;
    --venue-gold: #8a6238;
    --venue-amber: #a67a4a;
    --venue-brown: #5a3a26;
  }
  * { margin: 0; padding: 0; box-sizing: border-box; }
  html, body { width: 800px; height: 1200px; overflow: hidden; background: var(--page-bg); }
  .canvas { position: relative; width: 800px; height: 1200px; background: var(--page-bg); }
  .poster {
    position: absolute; left: 53px; top: 68px; width: 692px; height: 1068px;
    background: var(--paper);
    box-shadow: 0 18px 30px rgba(60, 90, 120, 0.18);
    overflow: hidden;
  }
  .venue-photo {
    position: absolute; left: 0; top: 0; width: 692px; height: 1001px;
    background:
      radial-gradient(ellipse 180px 90px at 50% 12%, rgba(190,150,200,0.55), transparent 70%),
      linear-gradient(180deg, var(--venue-deep) 0%, var(--venue-red) 18%, var(--venue-violet) 34%, var(--venue-gold) 52%, var(--venue-amber) 68%, var(--venue-brown) 100%);
  }
  .brand-mark {
    position: absolute; left: 292px; top: 60px; width: 108px; height: 108px;
    border: 10px solid var(--ink-light); border-radius: 50%;
  }
  .brand-name {
    position: absolute; left: 0; top: 182px; width: 692px; text-align: center;
    font-family: 'Poppins', sans-serif; font-weight: 700; font-size: 25px; line-height: 30px;
    color: var(--ink-light); letter-spacing: 0.5px;
  }
  .brand-sub {
    position: absolute; left: 0; top: 214px; width: 692px; height: 22px;
    display: flex; align-items: center; justify-content: center; gap: 10px;
  }
  .brand-sub__text {
    font-family: 'Poppins', sans-serif; font-weight: 400; font-size: 15px; line-height: 22px;
    letter-spacing: 7px; margin-right: -7px; color: var(--ink-light);
  }
  .brand-sub__rule { width: 62px; height: 2px; background: var(--ink-light); }
  .headline-script {
    position: absolute; left: 0; top: 338px; width: 692px; text-align: center;
    font-family: 'Great Vibes', cursive; font-size: 122px; line-height: 1; color: var(--ink-light);
  }
  .headline-main {
    position: absolute; left: 0; top: 431px; width: 692px; text-align: center;
    font-family: 'Bebas Neue', sans-serif; font-size: 171px; line-height: 1; letter-spacing: -2px;
    color: var(--ink-light);
  }
  .headline-rule { position: absolute; left: 229px; top: 594px; width: 238px; height: 1px; background: var(--ink-light); }
  .pitch {
    position: absolute; left: 0; top: 607px; width: 692px; text-align: center;
    font-family: 'Poppins', sans-serif; font-size: 25px; line-height: 29px; color: var(--ink-light);
  }
  .apply-pill {
    position: absolute; left: 36px; top: 825px; width: 628px; height: 86px;
    background: var(--brand-blue); border-radius: 43px;
    color: var(--ink-light); text-align: center;
  }
  .apply-pill__label { display: block; margin-top: 6px; font-family: 'Bebas Neue', sans-serif; font-size: 44px; line-height: 44px; }
  .apply-pill__email { display: block; font-family: 'Poppins', sans-serif; font-weight: 300; font-size: 21px; line-height: 26px; }
  .web-band {
    position: absolute; left: 0; top: 1001px; width: 692px; height: 67px;
    display: flex; align-items: center; justify-content: center;
    font-family: 'Poppins', sans-serif; font-weight: 600; font-size: 26px; color: var(--brand-blue); letter-spacing: 0.5px;
  }
</style>
</head>
<body>
<div class="canvas">
  <div class="poster">
    <div class="venue-photo" role="img" aria-label="Photo of ornate historic downtown theater interiors with domed ceiling, gilded arches and red stage curtains"></div>

    <div class="brand-mark"></div>
    <div class="brand-name">LANTERN STAGEHAND</div>
    <div class="brand-sub">
      <span class="brand-sub__rule"></span>
      <span class="brand-sub__text">COLLECTIVE</span>
      <span class="brand-sub__rule"></span>
    </div>

    <div class="headline-script">Has Open</div>
    <div class="headline-main">POSITION</div>
    <div class="headline-rule"></div>

    <p class="pitch">We are looking for talented Technicians<br>to add to our Roster of skilled professionals.</p>

    <div class="apply-pill">
      <span class="apply-pill__label">SEND RESUME TO:</span>
      <span class="apply-pill__email">APPLY@KRTCREW.EXAMPLE</span>
    </div>

    <div class="web-band">WWW.KRTCREW.EXAMPLE</div>
  </div>
</div>
</body>
</html>
```